Bring me business with this creative business card

Design my new business card. I am looking for something different with an impact. People will take a look at this card & they will 1- see how different & creative I am, 2-understand what I do 3- Call me to meet me!

I make videos with a message, testimonials. I am dynamic, fun, creative & human. My new website is in construction but in the meantime you can check this old one: brightpath.ca & another one Tidebloom.com & tidebloom facebook page.
I make videos. sometimes with a cameraman, sometimes with my phone. As an ex Public Relations agent, the message is the most important thing for me. I want to make my clients shine! When they start with me they often remind me of a lamb, when I finish coaching them they are powerful like LIONS! That's why I need a powerful business card!

Target Market(s)

Entrepreneurs, solo entrepreneurs, small & medium companies & start ups. People i will meet while networking. People that need videos on their website & social Networks to get attention, to be visible. men & women. From 35 to 49 years old.
I am an ex Public relations agent. I used to send clients in traditional medias, now with videos they have more chances to be seen on google the new media. I do videos of the president, his team, his loyal clients saying how great the company is & expert videos like series so people can be seen for example every 1 st of every month with a short 2 minute video. Also with my 20 years in marketing & communications I can coach & give tips to anybody who needs it.
Target: anybody who would like my old website brightpath.ca & I also have another website but it will be off line soon: tidebloom.com could give you ideas.

Industry/Entity Type

Communications

Contact Information for Business Card

I am in Montreal,So the business cards have to be the usual size like we have in Montreal: 9 cm x 5 cm
Details:My text: Mathilde Tessier Communication coach/Lead Storyteller. "CRAFTING VIDEOS AS BOLD AS YOU" off: 514-555-0147 cell: 514-555-0183. tidebloom.com
mathilde@tidebloom.com logo facebook, youtube, instagram

Colors
f37122

Requirements
Must have
• Dynamic, happy. Orange. Be creative in the look but NOT the shape of the card. Easy to read. Big enough to read.
Should not have
• No funny shapes: no round, no square, just the usual. I love creative but NOT on shape.

```html
<!DOCTYPE html>
<html lang="en">
<head>
<meta charset="utf-8">
<title>Tidebloom business card</title>
<link href="https://fonts.googleapis.com/css2?family=Tinos:wght@400;700&family=Open+Sans:wght@400&display=swap" rel="stylesheet">
<style>
  :root {
    --backdrop: #e4e4e4;
    --card-white: #f8f8f8;
    --brand-orange: #f37122;
    --brand-red: #ec5a22;
    --amber: #f3a020;
    --gold: #f7a92a;
    --ink: #222222;
    --white: #ffffff;
  }
  * { margin: 0; padding: 0; box-sizing: border-box; }
  html, body { width: 1200px; height: 900px; overflow: hidden; }
  body {
    background: var(--backdrop);
    position: relative;
    font-family: "Open Sans", Arial, sans-serif;
  }
  .card {
    position: absolute;
    top: 306px;
    width: 439px;
    height: 271px;
  }
  .card-front { left: 150px; background: var(--card-white); }
  .card-back {
    left: 609px;
    background: radial-gradient(ellipse at 50% 45%, var(--gold) 0%, #f48a24 45%, var(--brand-red) 100%);
    color: var(--white);
    text-align: center;
  }
  .brand-name {
    font-family: "Tinos", "Times New Roman", serif;
    font-weight: 700;
    line-height: 1;
  }
  .card-front .brand-name {
    position: absolute; left: 20px; top: 47px;
    font-size: 28px; color: var(--brand-red);
  }
  .motto {
    display: flex; align-items: center; gap: 3px;
    font-size: 12px; line-height: 1; white-space: nowrap;
  }
  .motto::before, .motto::after {
    content: ""; height: 1px; width: 22px; background: currentColor;
  }
  .card-front .motto {
    position: absolute; left: 22px; top: 77px; color: var(--amber);
  }
  .person-name {
    position: absolute; left: 21px; top: 128px;
    font-family: "Tinos", "Times New Roman", serif; font-weight: 700;
    font-size: 17px; color: var(--amber); letter-spacing: 0.5px;
  }
  .person-role {
    position: absolute; left: 21px; top: 148px;
    font-size: 12px; color: var(--ink);
  }
  .contact-list {
    position: absolute; left: 21px; top: 180px; list-style: none;
  }
  .contact-list li {
    display: flex; align-items: center; gap: 5px;
    font-size: 12px; color: var(--ink); height: 16px;
  }
  .contact-list svg { width: 10px; height: 10px; flex: none; }
  .art-front {
    position: absolute; left: 240px; top: 29px; width: 176px; height: 218px;
    background: linear-gradient(160deg, #f89a1c 0%, #fbc02d 50%, #f37122 100%);
    border-radius: 30% 30% 40% 40%;
  }
  .art-back {
    position: absolute; left: 176px; top: 44px; width: 88px; height: 115px;
    background: linear-gradient(160deg, #f89a1c 0%, #fbc02d 55%, #f37122 100%);
    border: 2px solid var(--white);
    border-radius: 30% 30% 40% 40%;
  }
  .card-back .brand-name {
    position: absolute; left: 0; right: 0; top: 165px; font-size: 28px;
  }
  .card-back .motto {
    position: absolute; left: 0; right: 0; top: 195px; justify-content: center;
  }
  .slogan {
    position: absolute; left: 0; right: 0; top: 234px;
    font-family: "Tinos", "Times New Roman", serif; font-size: 12.5px; letter-spacing: 0.3px;
  }
</style>
</head>
<body>
  <section class="card card-front">
    <div class="brand-name">TIDEBLOOM</div>
    <div class="motto">1 STORY 1 VOICE</div>
    <div class="person-name">MATHILDE T</div>
    <div class="person-role">Communication Coach/Lead Storyteller</div>
    <ul class="contact-list">
      <li><svg viewBox="0 0 10 10"><path d="M1 4 Q5 1 9 4 L8 5 L6 4 V3 H4 V4 L2 5 Z M2 6 H8 V9 H2 Z" fill="#f37122"/></svg>514-555-0147</li>
      <li><svg viewBox="0 0 10 10"><rect x="3" y="0.5" width="4.5" height="9" rx="1" fill="none" stroke="#f37122" stroke-width="1.2"/></svg>514-555-0183</li>
      <li><svg viewBox="0 0 10 10"><rect x="0.5" y="2" width="9" height="6.5" fill="#f37122"/><path d="M0.5 2 L5 6 L9.5 2" fill="none" stroke="#fff" stroke-width="0.9"/></svg>mathilde@tidebloom.com</li>
      <li><svg viewBox="0 0 10 10"><circle cx="5" cy="5" r="4.5" fill="#f37122"/></svg>www.tidebloom.com</li>
    </ul>
    <div class="art-front" role="img" aria-label="Low-poly geometric lion head illustration in orange and yellow"></div>
  </section>

  <section class="card card-back">
    <div class="art-back" role="img" aria-label="Small low-poly lion head illustration with white outline"></div>
    <div class="brand-name">TIDEBLOOM</div>
    <div class="motto">1 STORY 1 VOICE</div>
    <div class="slogan">CRAFTING VIDEOS AS BOLD AS YOU</div>
  </section>
</body>
</html>
```